Pellmora Business Cards

Create new business cards with the details below.

Stuart Kovan
Director

MB: +61 427 315 964
PH: 1300 647 519
Email: stuart.kovan@pellmora.com.au
Address: 27D Halden Parade, Brookvale VIC 3174 Australia
Website: www.pellmora.com.au

Target Market(s)

Other business

Industry/Entity Type

Business

Requirements
Must have
• must be clean looking

```html
<!DOCTYPE html>
<html lang="en">
<head>
<meta charset="utf-8">
<title>Pellmora Business Cards</title>
<link rel="stylesheet" href="https://fonts.googleapis.com/css2?family=Roboto:wght@300;400;500;700&display=swap">
<style>
  :root {
    --page: #e4e5e7;
    --charcoal: #333333;
    --band: #2f2f30;
    --lime: #9acd32;
    --lime-deep: #7aa62a;
    --white: #ffffff;
    --muted: #c9c9c9;
    --wood-light: #a9a6a2;
    --wood-mid: #8c8985;
    --wood-dark: #6f6c69;
  }
  * { margin: 0; padding: 0; box-sizing: border-box; }
  html, body { width: 1200px; height: 1200px; overflow: hidden; }
  body {
    background: var(--page);
    font-family: "Roboto", sans-serif;
    position: relative;
  }
  .card {
    position: absolute;
    left: 163px;
    width: 708px;
    height: 394px;
    overflow: hidden;
    box-shadow: 0 18px 30px rgba(0,0,0,0.28);
  }
  .card--back { top: 115px; }
  .card--front { top: 601px; }

  .wood {
    position: absolute;
    background: linear-gradient(180deg, var(--wood-light) 0%, var(--wood-mid) 45%, var(--wood-light) 70%, var(--wood-dark) 100%);
  }
  .card--back .wood { inset: 0; }

  .brand {
    position: absolute;
    left: 53px;
    top: 142px;
    display: flex;
    align-items: center;
    gap: 18px;
  }
  .brand__square {
    width: 96px;
    height: 96px;
    background: var(--charcoal);
  }
  .brand__text { display: flex; flex-direction: column; }
  .brand__name {
    font-weight: 700;
    font-size: 78px;
    line-height: 0.9;
    letter-spacing: 1px;
    color: var(--lime);
  }
  .brand__tagline {
    margin-top: 12px;
    font-weight: 500;
    font-size: 28px;
    letter-spacing: 3px;
    color: #1e1e1e;
  }
  .web-band {
    position: absolute;
    left: 0; right: 0;
    top: 342px;
    height: 25px;
    background: var(--band);
    text-align: center;
    font-weight: 700;
    font-size: 17px;
    line-height: 25px;
    color: var(--white);
  }
  .web-band__tld { color: var(--lime); font-size: 12px; }

  .card--front .wood--left { left: 0; top: 0; width: 122px; height: 100%; }
  .card--front .wood--right { left: 563px; top: 0; width: 145px; height: 100%; }
  .accent-stripe {
    position: absolute;
    left: 122px; top: 0;
    width: 22px; height: 100%;
    background: linear-gradient(180deg, var(--lime) 0%, var(--lime-deep) 100%);
  }
  .info-panel {
    position: absolute;
    left: 144px; top: 0;
    width: 419px; height: 100%;
    background: var(--charcoal);
    color: var(--white);
  }
  .person { position: absolute; left: 38px; top: 98px; }
  .person__name { font-weight: 300; font-size: 28px; letter-spacing: -0.5px; color: #e6e6e6; }
  .person__role { font-weight: 400; font-size: 20px; color: var(--lime); margin-top: -2px; }

  .contact { position: absolute; left: 38px; top: 248px; }
  .contact__icon { position: absolute; left: 0; top: 18px; }
  .contact__lines { margin-left: 34px; font-size: 15.5px; line-height: 21.5px; }
  .contact__label { color: var(--lime); font-weight: 300; }
  .address {
    position: absolute;
    left: 38px; top: 321px;
    font-weight: 300;
    font-size: 15px;
    letter-spacing: -0.3px;
    color: var(--muted);
  }
</style>
</head>
<body>
  <section class="card card--back" aria-label="Business card back">
    <div class="wood" role="img" aria-label="Weathered grey wooden planks background"></div>
    <div class="brand">
      <div class="brand__square"></div>
      <div class="brand__text">
        <span class="brand__name">PELLMORA</span>
        <span class="brand__tagline">PLANTATION SHUTTERS</span>
      </div>
    </div>
    <div class="web-band">PELLMORA<span class="web-band__tld">.COM.AU</span></div>
  </section>

  <section class="card card--front" aria-label="Business card front">
    <div class="wood wood--left" role="img" aria-label="Weathered grey wooden planks"></div>
    <div class="accent-stripe"></div>
    <div class="info-panel">
      <div class="person">
        <div class="person__name">Stuart Kovan</div>
        <div class="person__role">Director</div>
      </div>
      <div class="contact">
        <svg class="contact__icon" width="24" height="44" viewBox="0 0 24 44" aria-hidden="true">
          <rect x="1.5" y="1.5" width="21" height="41" rx="3" fill="none" stroke="#ffffff" stroke-width="2"/>
          <line x1="2" y1="7" x2="22" y2="7" stroke="#ffffff" stroke-width="1.5"/>
          <line x1="2" y1="35" x2="22" y2="35" stroke="#ffffff" stroke-width="1.5"/>
          <circle cx="12" cy="39" r="1.5" fill="#ffffff"/>
        </svg>
        <div class="contact__lines">
          <div>stuart.kovan@pellmora.com.au</div>
          <div><span class="contact__label">MB:</span> +61 427 315 964</div>
          <div><span class="contact__label">PH:</span> 1300 647 519</div>
        </div>
      </div>
      <div class="address">27D Halden Parade, Brookvale VIC 3174, Australia</div>
    </div>
    <div class="wood wood--right" role="img" aria-label="Weathered grey wooden planks"></div>
  </section>
</body>
</html>
```